Schriftdesign für Shop-Header Bild (Schmuckhandel) / Online-Marketing Material
Wir verkaufen Schmuck im Onlineshop mit Herz
Wir benötigen den vorgegebenen Text in schöner Form, Farbe und Größe harmonisch eingefügt, in unserem Bild.
Folgender Text soll sich schick ins Bild einfügen oder in 3-D vielleicht in Schriftfarbe gold hervorheben:
Mit ganzem Herzen für Sie da!
Ihr Online -Juwelier mit Herz
Siehe auch unser altes Bild mit Text, im Shop, wie es nicht aussehen sollte: www.sonnenflocke.de

```html
<!DOCTYPE html>
<html lang="de">
<head>
<meta charset="utf-8">
<title>Mit ganzem Herzen für Sie da – Shop-Header</title>
<link rel="stylesheet" href="https://fonts.googleapis.com/css2?family=Mr+Dafoe&family=Fira+Sans+Condensed:wght@500&display=block">
<style>
  :root {
    --page-bg: #ffffff;
    --satin-white: #f7f4ef;
    --satin-cream: #ece3d2;
    --gold-warm: #e3c27a;
    --beige: #cfbf9f;
    --brown-text: #6a3814;
  }
  * { margin: 0; padding: 0; box-sizing: border-box; }
  html, body {
    width: 1200px;
    height: 1200px;
    overflow: hidden;
    background: var(--page-bg);
  }
  .canvas {
    position: relative;
    width: 1200px;
    height: 1200px;
  }
  .header-banner {
    position: absolute;
    left: 40px;
    top: 496px;
    width: 1120px;
    height: 207px;
    overflow: hidden;
  }
  .banner-photo {
    position: absolute;
    inset: 0;
    background:
      radial-gradient(ellipse 90px 80px at 420px 100px, rgba(227,194,122,0.85), rgba(227,194,122,0) 70%),
      linear-gradient(160deg, rgba(255,255,255,0) 40%, rgba(201,184,147,0.35) 60%),
      linear-gradient(90deg, var(--satin-white) 0%, var(--satin-cream) 38%, var(--beige) 56%, var(--beige) 100%);
  }
  .headline {
    position: absolute;
    right: 241px;
    font-family: "Mr Dafoe", "Yellowtail", cursive;
    font-weight: 400;
    color: var(--brown-text);
    font-size: 66px;
    line-height: 1;
    white-space: nowrap;
    text-align: right;
  }
  .headline-first { top: 28px; }
  .headline-second { top: 78px; }
  .tagline {
    position: absolute;
    right: 249px;
    top: 158px;
    font-family: "Fira Sans Condensed", sans-serif;
    font-weight: 500;
    font-size: 21px;
    line-height: 1;
    letter-spacing: 1.6px;
    color: var(--brown-text);
    white-space: nowrap;
  }
</style>
</head>
<body>
  <main class="canvas">
    <section class="header-banner">
      <div class="banner-photo" role="img" aria-label="Goldener Herzanhänger an feiner Kette auf weißem Satin, rechts in warmes Beige übergehend"></div>
      <h1 class="headline headline-first">Mit ganzem Herzen</h1>
      <p class="headline headline-second">für Sie da!</p>
      <p class="tagline">Ihr Online-Juwelier mit Herz</p>
    </section>
  </main>
</body>
</html>
```